Modern web-site for a game changer new health app!

We need a very clean UX / UI design for our company website that will be used to sell our brand to large corporations and their employees. If we find a good match, we'd need you to do the app design and some graphics for ongoing design needs.

For a first of its kind app developed at Brockwell University, making licensed holistic medicine accessible to everyday people through access and curation by democratizing holistic health.

Please read the details attached thoroughly and reach out if you have any questions. Many thanks!
Updates

I've updated our requirements to make it easier, please review new details in the PDF shared. Many thanks!

Final brief refinement just uploaded, much has been simplified with very clear guidelines, please update and apply. thanks much!

Target Market(s)

corporate employees and large C level corporate leaders

Industry/Entity Type

wellness

Number of Pages Required

4 page

Font styles to use
Other font styles liked:
• We need website design now and app and socials after, hoping the designer we choose now can work with us on a regular basis going forward

Requirements
Must have
• clean, modern, minimal rich
Nice to have
• some added touches to give a custom feel
Should not have
• pictures, natural looking images or shapes

```html
<!DOCTYPE html>
<html lang="en">
<head>
<meta charset="utf-8">
<title>Ovela — Wellness for Everyone</title>
<link href="https://fonts.googleapis.com/css2?family=Lexend:wght@300;400;500;600&display=swap" rel="stylesheet">
<style>
:root{
  --orange:#f5a623;
  --orange-deep:#e08a12;
  --ink:#1f1a17;
  --dark:#2c241f;
  --cream:#fdf2d9;
  --grey-bg:#f2f2f2;
  --muted:#555;
  --line:#d9d9d9;
  --white:#fff;
}
*{box-sizing:border-box;margin:0;padding:0}
html,body{width:1200px;height:4839px;overflow:hidden}
body{position:relative;background:var(--white);font-family:'Lexend',sans-serif;color:var(--ink)}
.abs{position:absolute}
.accent{color:var(--orange)}
.h2{font-size:26px;font-weight:500;text-transform:uppercase;line-height:48px}
.btn{position:absolute;display:flex;align-items:center;justify-content:center;background:var(--orange);color:var(--ink);font-size:12px;text-transform:uppercase;border-radius:4px 14px 4px 14px;font-weight:400}
.wordmark{font-weight:500;color:var(--orange);letter-spacing:2px}

/* nav */
.nav .logo{left:112px;top:22px;font-size:40px}
.nav a{position:absolute;top:36px;font-size:13px;color:var(--ink);text-decoration:none;text-transform:uppercase}
.nav a.active{color:var(--orange)}

/* hero */
.hero{left:112px;top:86px;width:976px;height:464px;border-radius:0 90px 0 90px;background:radial-gradient(circle at 25% 35%,#3a4a36 0,#161a14 45%,#0b0c0a 100%);color:var(--white);text-align:center}
.hero h1{position:absolute;top:112px;width:100%;font-size:31px;font-weight:500}
.hero .tag{position:absolute;top:182px;width:100%;font-size:20px;font-weight:400}
.hero .sub{position:absolute;top:238px;width:100%;font-size:15px;font-weight:300}

/* steps */
.step{top:578px;height:294px;border:1px solid #eee;border-radius:8px;box-shadow:0 2px 6px rgba(0,0,0,.08);background:var(--white);padding:0 22px}
.step .num{position:absolute;right:0;top:0;width:56px;height:56px;background:var(--orange);border-radius:0 8px 0 18px;display:flex;align-items:center;justify-content:center;font-size:16px;font-weight:500}
.step h3{position:absolute;left:22px;top:102px;font-size:16px;font-weight:400;text-transform:uppercase;line-height:30px}
.step p{position:absolute;left:22px;right:20px;font-size:12.5px;color:var(--muted);line-height:32px;font-weight:300}
.step .icon{position:absolute;left:22px;top:28px}
.step.video{background:linear-gradient(120deg,#2a2420 0,#3d332b 60%,#5a4a3c 100%);border:none;border-radius:8px 8px 8px 60px;color:var(--white)}
.step.video h3{color:var(--orange);top:122px}
.step.video p{color:var(--white);top:165px}

/* enterprise */
.enterprise{left:0;top:953px;width:1200px;height:462px;background:var(--cream);border-radius:0 0 0 90px}
.copy p{font-size:14px;line-height:34px;font-weight:300}
.photo{background:linear-gradient(135deg,#c9d3dc,#8aa0b5 50%,#3d4b5c)}
.enterprise-photo{left:600px;top:998px;width:488px;height:450px;border-radius:280px 0 280px 0;border-top:4px solid var(--orange-deep);border-bottom:4px solid var(--orange-deep)}

/* how it works */
.how{left:0;top:1505px;width:1200px;text-align:center}
.how p{font-size:14px;line-height:34px;font-weight:300}
.how-box{top:1730px;width:273px;height:175px;border-radius:26px 4px 26px 4px;box-shadow:0 2px 8px rgba(0,0,0,.12);background:var(--white);text-align:center;font-size:17px;text-transform:uppercase;line-height:32px}
.how-box .icon{position:absolute;left:50%;transform:translateX(-50%);top:32px}
.connector{top:1817px;height:1px;width:60px;background:#ddd}

/* trust */
.trust{left:0;top:2072px;width:1200px;height:625px;background:var(--dark);border-radius:0 90px 0 0}
.trust-photo-a{left:112px;top:2150px;width:354px;height:468px;border-radius:44px 4px 44px 4px;background:linear-gradient(180deg,#c8a878 0,#e9c27d 40%,#6c5a44 75%,#3b3128 100%)}
.trust-photo-b{left:490px;top:2352px;width:226px;height:265px;border-radius:40px 4px 4px 4px;background:linear-gradient(135deg,#6b7a5a,#c8a887 60%,#8b6a55)}
.trust h2{position:absolute;left:600px;top:2132px;color:var(--white);font-size:27px;font-weight:500;line-height:50px;text-transform:uppercase}
.trust li{position:absolute;left:775px;list-style:none;color:var(--white);font-size:14px;text-transform:uppercase}
.trust li::before{content:"";position:absolute;left:-24px;top:6px;width:6px;height:6px;border-radius:50%;background:var(--orange)}
.partner{left:776px;top:2548px;width:284px;height:42px;background:var(--white);display:flex;align-items:center;justify-content:center;font-size:22px;font-weight:600;color:#111}

/* stats */
.proof{left:0;top:2768px;width:1200px;text-align:center}
.stat-num{font-size:28px;color:var(--orange);font-weight:500}
.stat-label{font-size:13.5px;line-height:33px;text-transform:uppercase;text-align:left}
.vdivider{width:1px;height:78px;background:#ccc;top:2945px}

/* human care */
.human{left:0;top:3093px;width:1200px;height:394px;background:var(--cream);border-radius:0 0 0 90px}
.human-art{left:665px;top:3130px;width:425px;height:320px;border-radius:8px;background:radial-gradient(circle at 60% 45%,#d9a44a 0,#b9852f 35%,rgba(253,242,217,0) 72%)}

/* testimonial */
.quote-mark{font-size:90px;color:var(--orange);font-weight:600;line-height:1}
.testimonial{left:250px;top:3540px;width:700px;text-align:center}
.stars{color:var(--orange);font-size:24px;letter-spacing:6px}
.testimonial h4{font-size:17px;font-weight:400;margin-top:20px;text-transform:uppercase}
.testimonial p{font-size:14.5px;line-height:34px;font-weight:300;margin-top:20px}
.testimonial .date{font-size:14px;margin-top:20px;text-transform:uppercase}
.arrow{top:3706px;font-size:26px;color:var(--ink)}

/* contact */
.contact{left:0;top:3968px;width:1200px;height:660px;background:var(--grey-bg);text-align:center}
.contact .lead{font-size:14px;line-height:34px;font-weight:300}
.field{position:absolute;border:1px solid #9a9a9a;height:46px}
.field span{position:absolute;left:24px;top:-9px;background:var(--grey-bg);padding:0 6px;font-size:11.5px;text-transform:uppercase}

/* footer */
.footer{left:0;top:4612px;width:1200px;height:227px;background:var(--dark);border-radius:0 90px 0 0}
.footer .logo{left:150px;top:50px;font-size:52px}
.footer .copy-line{left:150px;top:156px;font-size:13px;color:var(--white);text-transform:uppercase}
.social{top:102px;width:32px;height:32px;border:1.5px solid var(--white);border-radius:50%}
</style>
</head>
<body>

<header class="nav">
  <div class="abs logo wordmark">OVELA</div>
  <a class="active" style="left:468px">Home</a>
  <a style="left:545px">Complementary</a>
  <a style="left:707px">Enterprise</a>
  <a style="left:830px">Members</a>
  <span class="btn" style="left:956px;top:26px;width:132px;height:36px">Get Started</span>
</header>

<section class="abs hero" role="img" aria-label="Hero photograph of white flower blossoms on a dark background">
  <h1><span class="accent">WELLNESS</span> FOR EVERYONE</h1>
  <div class="tag">MODERN SCIENCE MEETS ANCIENT WISDOM</div>
  <div class="sub">Get 1 on 1 PHD care on US for personalized remedies</div>
  <span class="btn" style="left:421px;top:304px;width:133px;height:40px">Get Started</span>
</section>

<article class="abs step" style="left:112px;width:228px">
  <svg class="icon" width="48" height="52" viewBox="0 0 48 52" fill="none" stroke="#d18a1a" stroke-width="1.6"><rect x="2" y="2" width="36" height="46"/><path d="M8 16h24M8 24h24M8 32h16M8 40h12"/><path d="M30 44l14-16 3 3-14 16-5 1z"/></svg>
  <span class="num">01</span>
  <h3>Take Test</h3>
  <p style="top:140px">Sed ornare, turpis eu aliquet placerat, nisi erat pharetra nunc, ac lacinia massa urna ut diam.</p>
</article>
<article class="abs step" style="left:358px;width:227px">
  <svg class="icon" width="48" height="52" viewBox="0 0 48 52" fill="none" stroke="#d18a1a" stroke-width="1.6"><circle cx="24" cy="16" r="8"/><path d="M10 38c2-8 8-12 14-12s12 4 14 12"/><rect x="6" y="38" width="36" height="10" rx="3"/></svg>
  <span class="num">02</span>
  <h3>Get matched with<br>a specialist</h3>
  <p style="top:170px">Sed ornare, turpis eu aliquet placerat, nisi erat pharetra nunc, ac lacinia massa.</p>
</article>
<article class="abs step video" style="left:605px;width:483px" role="img" aria-label="Photograph of a person on a video consultation">
  <span class="num">03</span>
  <h3>Video Consult</h3>
  <p>To get full read on your unique needs + natural remedies - diet -lifestyle - exercise - home &amp; body care - meditation - yoga</p>
</article>

<section class="abs enterprise"></section>
<div class="abs copy" style="left:112px;top:995px;width:440px">
  <h2 class="h2"><span class="accent">OVELA</span> FOR ENTERPRISE</h2>
  <p style="font-size:15px;font-weight:400;margin-top:8px;text-transform:uppercase">We're all feeling a strain on our health these days</p>
  <p style="margin-top:12px">Leaders of industry aren't accidental, they know employee retention &amp; experience work in their favor.</p>
  <p style="margin-top:12px">In these tumultuous times, Solace brings much-needed relief and benefits to teams that bring their all in return.</p>
</div>
<span class="btn" style="left:112px;top:1323px;width:190px;height:40px">Ovela for Enterprise</span>
<div class="abs photo enterprise-photo" role="img" aria-label="Photograph of a doctor reviewing a clipboard with a senior patient"></div>

<section class="abs how">
  <h2 class="h2"><span class="accent">HOW</span> IT WORKS</h2>
  <p style="margin-top:10px">Sign-up and get a full read of your unique constitution and what makes it thrive with a custom plan made<br>one on one with your on-demand holistic Doctor/Educator.</p>
  <p style="margin-top:12px">Unlimited texting to address your plan or any other concern you have about your health.</p>
</section>
<div class="abs how-box" style="left:130px"><svg class="icon" width="48" height="48" viewBox="0 0 48 48" fill="none" stroke="#d18a1a" stroke-width="1.6"><rect x="4" y="6" width="30" height="38"/><path d="M10 16h18M10 24h18M10 32h10"/><path d="M28 40l14-18 3 3-14 18-5 1z"/></svg><div style="margin-top:108px">Sign Up</div></div>
<div class="abs connector" style="left:403px"></div>
<div class="abs how-box" style="left:463px"><svg class="icon" style="top:18px" width="48" height="56" viewBox="0 0 48 56" fill="none" stroke="#d18a1a" stroke-width="1.6"><path d="M8 4h32v48H8z"/><path d="M14 14h20M14 22h20M14 30h20M14 38h12"/><circle cx="34" cy="44" r="5"/></svg><div style="margin-top:92px">Get a full read of<br>your constitution</div></div>
<div class="abs connector" style="left:736px"></div>
<div class="abs how-box" style="left:797px"><svg class="icon" width="48" height="48" viewBox="0 0 48 48" fill="none" stroke="#d18a1a" stroke-width="1.6"><rect x="6" y="4" width="34" height="40"/><path d="M23 14l8 5v9l-8 5-8-5v-9z"/><path d="M15 19l8 5 8-5M23 24v9"/></svg><div style="margin-top:108px">Get a custom plan</div></div>
<span class="btn" style="left:516px;top:1950px;width:166px;height:40px">View our plans</span>

<section class="abs trust">
  <h2 style="top:60px"><span class="accent">OUR CLIENTS TRUST US</span> TO PROVIDE<br>HOLISTIC HEALTH FOR THEIR TEAM,<br>SO SHOULD YOU!</h2>
  <ul>
    <li style="top:252px">Any challenge</li>
    <li style="top:306px">Anytime</li>
    <li style="top:360px">Anywhere</li>
  </ul>
  <div class="abs" style="left:776px;top:430px;font-size:13px;color:var(--orange)">TRUSTED BY:</div>
</section>
<div class="abs trust-photo-a" role="img" aria-label="Photograph of a person meditating on a lakeside dock at sunrise"></div>
<div class="abs trust-photo-b" role="img" aria-label="Photograph of two colleagues looking at a tablet"></div>
<div class="abs partner">Northfield Apparel</div>

<section class="abs proof">
  <h2 class="h2" style="font-size:26px"><span class="accent">CLINICALLY PROVEN TO HELP PEOPLE</span> NOT ONLY FEEL<br>BETTER, BUT THRIVE.</h2>
  <p style="font-size:16px;margin-top:28px;text-transform:uppercase;font-weight:300">Members love the easy &amp; effective experience.</p>
</section>
<div class="abs stat-num" style="left:115px;top:2963px">80%</div>
<div class="abs wordmark" style="left:208px;top:2960px;font-size:32px">OVELA</div>
<div class="abs vdivider" style="left:358px"></div>
<div class="abs stat-num" style="left:412px;top:2963px">20%</div>
<div class="abs stat-label" style="left:520px;top:2955px">Leading corporate<br>health programs</div>
<div class="abs vdivider" style="left:748px"></div>
<div class="abs stat-num" style="left:810px;top:2963px">5<span style="font-size:22px">★</span></div>
<div class="abs stat-label" style="left:890px;top:2955px">Average rating after<br>every care session.</div>

<section class="abs human"></section>
<div class="abs copy" style="left:112px;top:3130px;width:500px">
  <h2 class="h2"><span class="accent">HUMAN CARE</span> POWERED BY<br>TECHNOLOGY</h2>
  <p style="font-size:17px;font-weight:300;margin-top:18px;text-transform:uppercase">All your mind body needs met in one place</p>
  <p style="margin-top:10px;width:420px">All practitioners work collaboratively to provide the best care.</p>
</div>
<span class="btn" style="left:112px;top:3403px;width:131px;height:40px">Learn more</span>
<div class="abs human-art" role="img" aria-label="Illustration of a care team surrounded by connected devices"></div>

<div class="abs quote-mark" style="left:175px;top:3545px">“</div>
<section class="abs testimonial">
  <div class="stars">★★★★★</div>
  <h4>Marla | Human Resources | Northfield Apparel</h4>
  <p>Anytime I'm feeling tired or stressed I just get up and pass by the classes by Solace and I'm instantly perked up and happy again! Solace has been an excellent enhancement at Northfield Apparel and well needed for everyone. Employees rave about it and frequently ask for more to be added and are getting along better. Ultimately they are more excited about coming to work, automatically enhancing their performance.</p>
  <div class="date"><svg width="16" height="16" viewBox="0 0 16 16" fill="none" stroke="#f5a623" stroke-width="1.5" style="vertical-align:-2px;margin-right:12px"><rect x="1.5" y="3" width="13" height="11.5"/><path d="M1.5 7h13M5 1v4M11 1v4"/></svg>January 10, 2016</div>
</section>
<div class="abs quote-mark" style="left:978px;top:3850px">”</div>
<div class="abs arrow" style="left:110px">‹</div>
<div class="abs arrow" style="left:1075px">›</div>

<section class="abs contact">
  <h2 class="h2" style="margin-top:46px"><span class="accent">WE'D LOVE</span> TO HEAR FROM YOU</h2>
  <p class="lead" style="margin-top:10px">Tell us a little about you and your company to see if you qualify for our membership-based model at no<br>cost to your company.</p>
  <div class="field" style="left:124px;top:225px;width:463px"><span>Name</span></div>
  <div class="field" style="left:614px;top:225px;width:463px"><span>Email</span></div>
  <div class="field" style="left:124px;top:314px;width:463px"><span>How many people in your location?</span></div>
  <div class="field" style="left:614px;top:314px;width:463px"><span>How many locations?</span></div>
  <div class="field" style="left:124px;top:399px;width:953px;height:108px"><span>Anything else we can help you with?</span></div>
  <span class="btn" style="left:527px;top:542px;width:145px;height:38px">Send message</span>
</section>

<footer class="abs footer">
  <div class="abs logo wordmark">OVELA</div>
  <div class="abs copy-line">Copyright © <span class="accent">Ovela</span> 2025. All rights reserved</div>
  <span class="abs social" style="left:855px"></span>
  <span class="abs social" style="left:895px"></span>
  <span class="abs social" style="left:935px"></span>
  <span class="abs social" style="left:975px"></span>
  <span class="abs social" style="left:1015px"></span>
</footer>

</body>
</html>
```